Design letter head and business card

Hello,

you should design a business card and letter paper for Kranichflug Marketing. In German we write this word with K insteat of C.

Company does not have a logo. But in general, we write Kranichflug Marketing in 2 lines.
First line red: KRANICHFLUG
Second line gray: MARKETING

Red (or wine red) and Gray / Black are our favorite colors.

Company slogan: "Fresh Ground Online Marketing".

Company offers SEO, SEM, SEA, AdWords, Conversion Optimization, Online Markting Consulting ...

The website is old, please do not use this as base for your task.

German letter paper sizes:
Viawable Dimensions : 210 x 297 mm
Needed file dimensions: 212 x 299 mm

Informations to include:

Address:
Kranichflug Marketing GmbH
Lindenweg 23
71592 Weinstadt
Germany

Geschäftsführer | CEO: Bernhard Olzner

Phone: +49 (0) 7151 846 27 05

Fax: +49 (0) 7151 846 27 88

Mail: info@kranichflug-beispiel.de

Web: www.kranichflug-beispiel.de

Amtsgericht Suttgart, HRB 537264

Bank: Rosenauer Bank
IBAN: DE827315480900XXXXXXXX
BIC: GENODES1RSQ

Thanks

Bernhard

Target Market(s)

People who likes to win the online marketing game.

Industry/Entity Type

Business

Contact Information for Business Card

Here is the personal text on the card:

Name:
Bernhard Olzner

Title:
Geschäftsführer | CEO

Address:
Kranichflug Marketing GmbH
Lindenweg 23
71592 Weinstadt
Germany

Phone:
+49 (0) 7151 846 27 05

Fax:
+49 (0) 7151 846 27 88

Mail:
olzner@kranichflug-beispiel.de

Web:
www.kranichflug-beispiel.de

Business Card:
Viewable Dimensions: 85 x 55 mm
Needed file dimensions: 87 x 57mm

Font styles to use
Sans Serif

Requirements
Nice to have
• It would be great to see the dynamics of a helicopter.

```html
<!DOCTYPE html>
<html lang="de">
<head>
<meta charset="utf-8">
<title>Kranichflug Marketing – Briefpapier</title>
<link rel="stylesheet" href="https://fonts.googleapis.com/css2?family=Encode+Sans+Semi+Condensed:wght@400;700&family=Oswald:wght@300&display=swap">
<style>
  :root {
    --brand-red: #9e1b20;
    --ink: #2a2a2a;
    --ink-soft: #333333;
    --sheet: #ffffff;
    --edge: #cfcfcf;
  }
  * { margin: 0; padding: 0; box-sizing: border-box; }
  html, body { width: 851px; height: 1200px; overflow: hidden; background: var(--sheet); }
  .letterhead {
    position: relative;
    width: 851px;
    height: 1200px;
    background: var(--sheet);
    border: 1px solid var(--edge);
    font-family: "Encode Sans Semi Condensed", Arial, sans-serif;
    color: var(--ink);
  }
  .tagline-top {
    position: absolute;
    top: 41px;
    left: 556px;
    width: 258px;
    display: flex;
    align-items: center;
    gap: 11px;
    font-family: "Oswald", "Arial Narrow", sans-serif;
    font-weight: 300;
    font-size: 15px;
    color: var(--ink);
    white-space: nowrap;
  }
  .tagline-top .rule { flex: 1; height: 1px; background: var(--brand-red); }
  .brand {
    position: absolute;
    top: 138px;
    left: 36px;
    width: 156px;
  }
  .brand-name {
    font-weight: 700;
    font-size: 23px;
    line-height: 24px;
    letter-spacing: 0.5px;
    text-transform: uppercase;
    color: var(--ink);
  }
  .brand-slogan {
    margin-top: 10px;
    font-family: "Oswald", "Arial Narrow", sans-serif;
    font-weight: 300;
    font-size: 13.5px;
    white-space: nowrap;
    color: var(--ink);
  }
  .brand-rule {
    margin-top: 8px;
    width: 152px;
    height: 1px;
    background: var(--brand-red);
  }
  .sender-address {
    position: absolute;
    top: 232px;
    left: 37px;
    font-style: normal;
    font-size: 11.5px;
    line-height: 16.5px;
    color: var(--ink-soft);
  }
  .footer {
    position: absolute;
    left: 55px;
    width: 751px;
    top: 1125px;
    text-align: center;
    font-size: 12px;
    color: var(--ink-soft);
    white-space: nowrap;
  }
  .footer .rule { height: 2px; background: var(--brand-red); margin: 4px 0 6px; }
</style>
</head>
<body>
  <div class="letterhead">
    <div class="tagline-top">
      <span class="rule"></span>
      <span>Fresh Ground Online Marketing</span>
      <span class="rule"></span>
    </div>

    <header class="brand">
      <div class="brand-name">Kranichflug<br>Marketing</div>
      <div class="brand-slogan">Fresh Ground Online Marketing</div>
      <div class="brand-rule"></div>
    </header>

    <address class="sender-address">
      Kranichflug Marketing GmbH,<br>
      Lindenweg 23<br>
      71592 Weinstadt, Germany
    </address>

    <footer class="footer">
      <div>Phone: +49 (0) 7151 846 27 05; Fax: +49 (0) 7151 846 27 88; e-mail: info@kranichflug-beispiel.de; www.kranichflug-beispiel.de</div>
      <div class="rule"></div>
      <div>Amtsgericht Suttgart, HRB 537264; Bank: Rosenauer Bank; IBAN: DE827315480900XXXXXXXX; BIC: GENODES1RSQ</div>
    </footer>
  </div>
</body>
</html>
```